Web Design For Staffing Company

We need a homepage web design for a technical staffing company.

Please see attached brief for project details.

please make the site modern with bold colors while matching the logo

Be sure to read the attached breif in full beforehand.

Target Market(s)

technical companies looking to hire talent

Industry/Entity Type

Staffing

Number of Pages Required

1 page

Font styles to use
Sans Serif

```html
<!DOCTYPE html>
<html lang="en">
<head>
<meta charset="utf-8">
<title>Velora Staffing – Technical Staffing</title>
<link rel="stylesheet" href="https://fonts.googleapis.com/css2?family=Roboto:wght@400;500;700&family=Raleway:ital,wght@0,400;0,500;0,600;1,400;1,500&display=swap">
<style>
:root{
  --blue:#1e5a8c;
  --blue-btn:#235c8f;
  --blue-dark:#16466f;
  --ink:#222;
  --grey-text:#7a7a7a;
  --band:#f2f2f2;
  --footer:#2f2f30;
  --white:#fff;
}
*{margin:0;padding:0;box-sizing:border-box}
html,body{width:1200px;height:3953px;overflow:hidden;background:var(--white)}
body{position:relative;font-family:"Raleway",sans-serif;color:var(--ink)}
.abs{position:absolute}
.head-font{font-family:"Roboto",sans-serif}

/* header */
.site-header{left:0;top:0;width:1200px;height:101px;background:var(--white)}
.brand{left:95px;top:26px;display:flex;align-items:center;gap:10px;font-family:"Roboto",sans-serif;font-weight:700;font-size:30px;color:var(--blue)}
.brand-mark{width:22px;height:22px;border-radius:50%;background:var(--blue)}
.nav{top:40px;font-family:"Roboto",sans-serif;font-size:14px;color:#333}
.nav.active{color:var(--blue)}
.field{top:28px;height:38px;border:1px solid #bbb;font-size:15px;color:#999;display:flex;align-items:center;justify-content:center}
.search-btn{left:979px;top:28px;width:107px;height:38px;background:var(--blue);color:#fff;font-family:"Roboto",sans-serif;font-weight:500;font-size:13px;display:flex;align-items:center;justify-content:center}

/* hero */
.hero-photo{left:0;top:101px;width:1200px;height:556px;background:linear-gradient(120deg,#dfe5ea,#c9d2d9 55%,#f0f2f3)}
.hero-panel{left:0;top:101px;width:1200px;height:556px}
.hero-title{left:110px;top:255px;font-family:"Roboto",sans-serif;font-weight:700;font-size:46px;line-height:60px;color:#fff}
.hero-sub{left:110px;top:386px;font-family:"Roboto",sans-serif;font-size:15px;color:#fff}
.btn{display:flex;align-items:center;justify-content:center;font-family:"Roboto",sans-serif;font-weight:500;font-size:15px}
.btn-white{background:#fff;color:var(--blue)}
.btn-black{background:#2a2a2a;color:#fff}
.btn-blue{background:var(--blue-btn);color:#fff}

/* intro */
.intro{left:0;top:657px;width:1200px;height:164px;background:var(--band)}
.intro p{position:absolute;left:0;width:1200px;top:47px;text-align:center;font-size:15px;line-height:34px;color:var(--grey-text)}

/* feature rows */
.photo{background:linear-gradient(135deg,#cfd8df,#8fa4b5 60%,#5d7488)}
.frame{border:2px solid var(--blue)}
.copy{font-size:15.5px;line-height:34.2px;color:var(--grey-text);text-align:justify}

/* testimonial */
.testi{left:0;top:1978px;width:1200px;height:345px;background:linear-gradient(180deg,#1e2833,#2b3744 50%,#1c2530)}
.testi h2{position:absolute;top:52px;width:1200px;text-align:center;font-family:"Roboto",sans-serif;font-weight:700;font-size:42px;color:#fff}
.testi .quote{position:absolute;left:110px;width:980px;top:110px;text-align:center;font-style:italic;font-size:16px;line-height:34px;color:#fff}
.testi .name{position:absolute;top:236px;width:1200px;text-align:center;font-weight:600;font-size:15px;color:#fff}
.testi .role{position:absolute;top:266px;width:1200px;text-align:center;font-size:15px;color:#fff}

/* blog */
.blog-title{left:0;top:2412px;width:1200px;text-align:center;font-family:"Roboto",sans-serif;font-weight:700;font-size:42px;color:#222}
.card{width:474px;height:258px;background:#fff;box-shadow:0 0 6px rgba(0,0,0,.12)}
.card .thumb{position:absolute;left:0;top:0;width:236px;height:258px}
.card h3{position:absolute;left:249px;top:18px;width:212px;font-family:"Roboto",sans-serif;font-weight:500;font-size:14.5px;line-height:25px;color:#222}
.card .date{position:absolute;left:249px;top:78px;font-size:15px;color:#444}
.card .excerpt{position:absolute;left:249px;top:108px;width:212px;font-size:11.5px;line-height:24px;color:#8a8a8a;text-align:justify}
.card .go{position:absolute;right:7px;bottom:2px;width:43px;height:36px;background:var(--blue);display:flex;align-items:center;justify-content:center}

/* cta */
.cta{top:3219px;width:471px;height:312px;background:linear-gradient(160deg,#2c6396,#1f5584 60%,#2a5e8d)}
.cta h2{position:absolute;top:88px;width:100%;text-align:center;font-family:"Roboto",sans-serif;font-weight:500;font-size:25px;line-height:37px;color:#fff}
.cta .outline{position:absolute;left:137px;top:175px;width:199px;height:46px;border:2px solid #fff;color:#fff;font-family:"Roboto",sans-serif;font-weight:500;font-size:19px;display:flex;align-items:center;justify-content:center}

/* footer */
.site-footer{left:0;top:3634px;width:1200px;height:319px;background:var(--footer);color:#fff}
.fcol{position:absolute;top:64px}
.fcol h4{font-family:"Roboto",sans-serif;font-weight:500;font-size:15px}
.fcol p{margin-top:18px;font-size:15px;line-height:28px}
.fcol .btn{position:absolute;top:104px;width:140px;height:45px;font-size:15px}
.copyright{position:absolute;top:261px;width:1200px;text-align:center;font-size:15px}
</style>
</head>
<body>

<header class="abs site-header">
  <div class="abs brand"><span class="brand-mark"></span>Velora Staffing</div>
  <span class="abs nav active" style="left:324px">HOME</span>
  <span class="abs nav" style="left:391px">ABOUT</span>
  <span class="abs nav" style="left:463px">JOB SEEKERS</span>
  <span class="abs nav" style="left:577px">CLIENTS</span>
  <span class="abs nav" style="left:660px">CONTACT</span>
  <div class="abs field" style="left:749px;width:107px">Keyword</div>
  <div class="abs field" style="left:865px;width:106px">Location</div>
  <div class="abs search-btn">SEARCH JOBS</div>
</header>

<section>
  <div class="abs hero-photo" role="img" aria-label="Smiling support agent wearing a headset at a computer in a bright office"></div>
  <svg class="abs hero-panel" width="1200" height="556" viewBox="0 0 1200 556" aria-hidden="true">
    <polygon points="0,0 657,0 532,556 0,556" fill="#1e5a8c"/>
  </svg>
  <h1 class="abs hero-title">THE RIGHT PEOPLE<br>FOR THE RIGHT JOBS!</h1>
  <p class="abs hero-sub">BRIDGING THE TALENT GAP IN TECHNICAL STAFFING</p>
  <a class="abs btn btn-white" style="left:112px;top:433px;width:153px;height:50px">HIRE TALENT</a>
  <a class="abs btn btn-black" style="left:284px;top:433px;width:153px;height:50px">GET HIRED</a>
</section>

<section class="abs intro">
  <p>Velora Staffing is a National Technical Staffing and Recruiting Solutions Provider founded in 2013 focused on matching contract<br>and full time Engineering and IT professionals with new and exciting employment opportunities!</p>
</section>

<section>
  <div class="abs frame" style="left:129px;top:947px;width:446px;height:426px"></div>
  <div class="abs photo" style="left:112px;top:927px;width:447px;height:430px" role="img" aria-label="Engineer working on technical drawings at a desktop computer"></div>
  <p class="abs copy" style="left:605px;top:1002px;width:468px">WE LOVE TO RECRUIT! It's our passion and we take it very seriously! It is not easy for JOB SEEKERS to put their job search efforts and trust in the hands of someone else, especially when there are so many Staffing Firms to choose from. So how do you know you are choosing the best Staffing Representation possible?</p>
  <a class="abs btn btn-blue" style="left:603px;top:1218px;width:155px;height:51px">LEARN MORE</a>
  <a class="abs btn btn-blue" style="left:772px;top:1218px;width:155px;height:51px">VIEW JOBS</a>
</section>

<section>
  <p class="abs copy" style="left:115px;top:1499px;width:468px">Are you responsible for Technical Staffing within your organization? Are you satisfied with your current Supplier(s)' overall performance? Does it appear they identify potential Candidate(s) based purely on "buzz-word" searches? Is it evident they just do not grasp the scope and responsibilities of your technical staffing need(s)?</p>
  <a class="abs btn btn-blue" style="left:112px;top:1716px;width:155px;height:50px">LEARN MORE</a>
  <a class="abs btn btn-blue" style="left:282px;top:1716px;width:155px;height:50px">HIRE TALENT</a>
  <div class="abs frame" style="left:626px;top:1442px;width:445px;height:429px"></div>
  <div class="abs photo" style="left:641px;top:1424px;width:449px;height:428px" role="img" aria-label="Two colleagues reviewing work together on a computer screen"></div>
</section>

<section class="abs testi" role="region" aria-label="Testimonials">
  <h2>TESTIMONIALS</h2>
  <p class="quote">"Marcus Hale is an excellent recruiter. He is articulate, honest, has a good nature and is an effective information conduit between his clients and candidates. He gave me the feeling he is there for the big picture desiring to forge a future relationship that will be mutually beneficial to both of us."</p>
  <p class="name">Ben R.</p>
  <p class="role">Electrical Test Engineer in the Automotive Sector</p>
</section>

<h2 class="abs blog-title">VELORA BLOG</h2>

<article class="abs card" style="left:112px;top:2489px">
  <div class="thumb photo" role="img" aria-label="Woman working on a laptop"></div>
  <h3>WAYS TO MAKE THE MOST OF THE HOT JOB MARKET</h3>
  <p class="date">June 17, 2019</p>
  <p class="excerpt">This is the tightest labor market I can remember. Unemployment is at a 50-year low and wage growth is at 3.2%," said Dan Mercer, chief economist for Jobline.com</p>
  <span class="go"><svg width="22" height="14" viewBox="0 0 22 14"><path d="M1 7h19M14 1l6 6-6 6" stroke="#fff" stroke-width="2" fill="none"/></svg></span>
</article>
<article class="abs card" style="left:612px;top:2489px">
  <div class="thumb photo" role="img" aria-label="Two people shaking hands over a desk"></div>
  <h3>BACK TO BASICS: MEETING EMPLOYEES' NEEDS TO</h3>
  <p class="date">June 06, 2019</p>
  <p class="excerpt">The benefits of employee satisfaction are well-so HR professionals and leaders across all industries spend a great deal of maximizing those benefits</p>
  <span class="go"><svg width="22" height="14" viewBox="0 0 22 14"><path d="M1 7h19M14 1l6 6-6 6" stroke="#fff" stroke-width="2" fill="none"/></svg></span>
</article>
<article class="abs card" style="left:112px;top:2768px">
  <div class="thumb" style="background:linear-gradient(135deg,#3a3a3a,#9a9a9a 60%,#222)" role="img" aria-label="Black and white portrait with a quotation overlay"></div>
  <h3>5 IMPORTANT TAKEAWAYS FROM NEXORA'S</h3>
  <p class="date">May 20, 2019</p>
  <p class="excerpt">Recently, the folks at Nexora published their findings from a two-year study they conducted on remote work. The company is certainly</p>
  <span class="go"><svg width="22" height="14" viewBox="0 0 22 14"><path d="M1 7h19M14 1l6 6-6 6" stroke="#fff" stroke-width="2" fill="none"/></svg></span>
</article>
<article class="abs card" style="left:612px;top:2768px">
  <div class="thumb" style="background:linear-gradient(135deg,#1e1e1e,#7d7d7d 55%,#2a2a2a)" role="img" aria-label="Black and white portrait of a thoughtful older man"></div>
  <h3>TOP JOB INTERVIEW SOFT SKILL IS UNCOMFORTABLE</h3>
  <p class="date">May 14, 2019</p>
  <p class="excerpt">A survey published in Midland Business Review says that over two-thirds of managers (69%) are uncomfortable communicating with employees</p>
  <span class="go"><svg width="22" height="14" viewBox="0 0 22 14"><path d="M1 7h19M14 1l6 6-6 6" stroke="#fff" stroke-width="2" fill="none"/></svg></span>
</article>

<a class="abs btn btn-blue" style="left:503px;top:3055px;width:195px;height:60px">VIEW MORE BLOGS</a>

<section class="abs cta" style="left:112px" role="img" aria-label="Blue tinted photo of a professional in an office">
  <h2>LOOKING FOR CAREER-MINDED<br>CANDIDATES</h2>
  <span class="outline">REGISTER NOW</span>
</section>
<section class="abs cta" style="left:615px" role="img" aria-label="Blue tinted photo of a job seeker at work">
  <h2>LOOKING FOR CAREER<br>OPPORTUNITIES</h2>
  <span class="outline">SEARCH JOB</span>
</section>

<footer class="abs site-footer">
  <div class="fcol" style="left:112px">
    <h4>GET HIRED</h4>
    <p>Nemo enim ipsam voluptatem<br>quia voluptas sit aspernatur</p>
    <a class="btn btn-blue" style="left:-2px">SEARCH</a>
  </div>
  <div class="fcol" style="left:468px">
    <h4>HIRE TALENT</h4>
    <p>Nemo enim ipsam voluptatem<br>quia voluptas sit aspernatur</p>
    <a class="btn btn-blue" style="left:-2px">START NOW</a>
  </div>
  <div class="fcol" style="left:781px">
    <h4>ADDRESS</h4>
    <p>Velora Staffing, Inc. 120 Harbor Lane, Bldg.<br>2, 3rd floor Ashford, MA 01990</p>
    <a class="btn btn-blue" style="left:-2px">CONTACT US</a>
  </div>
  <p class="copyright">© 2020 All Rights Reserved</p>
</footer>

</body>
</html>
```